Email Banner (LoomDigest)

We require an email banner for our email promotions sent to prospect clients. The banner needs to contain the wording LoomDigest and use the same colour scheme as the logos attached.

This is for B2B professional's so needs to look like a place you would come to read technology articles.

```html
<!DOCTYPE html>
<html lang="en">
<head>
<meta charset="utf-8">
<title>LoomDigest Email Banner</title>
<link rel="stylesheet" href="https://fonts.googleapis.com/css2?family=Montserrat:ital,wght@0,400;0,500;0,600;0,700;1,600&display=swap">
<style>
  :root {
    --stage: #1c1c1c;
    --paper: #ffffff;
    --paper-shade: #e9ebec;
    --ink: #0d1a2b;
    --ink-soft: #2a3445;
    --green: #7cc242;
    --teal: #1e9b8c;
    --blue: #0a8fd6;
    --photo-light: #dfe4e6;
    --photo-mid: #8a98a6;
    --photo-dark: #2d3c52;
  }
  * { box-sizing: border-box; margin: 0; padding: 0; }
  html, body {
    width: 1200px;
    height: 661px;
    overflow: hidden;
    background: var(--stage);
    font-family: "Montserrat", Arial, sans-serif;
  }
  .banner {
    position: absolute;
    left: 30px;
    top: 127px;
    width: 1140px;
    height: 407px;
    background: linear-gradient(160deg, var(--paper) 35%, var(--paper-shade) 100%);
    overflow: hidden;
  }
  .banner-shapes {
    position: absolute;
    inset: 0;
    width: 1140px;
    height: 407px;
  }
  .brand {
    position: absolute;
    left: 41px;
    top: 46px;
    display: flex;
    align-items: center;
    gap: 10px;
  }
  .brand-mark {
    width: 18px;
    height: 18px;
    background: var(--green);
  }
  .brand-name {
    font-size: 33px;
    font-weight: 600;
    color: var(--ink);
    letter-spacing: -0.5px;
  }
  .headline {
    position: absolute;
    left: 40px;
    top: 140px;
    font-size: 45px;
    font-weight: 400;
    color: var(--ink);
    letter-spacing: 0.3px;
  }
  .headline strong { font-weight: 700; }
  .intro {
    position: absolute;
    left: 42px;
    top: 199px;
    width: 370px;
    font-size: 16.4px;
    line-height: 19px;
    font-weight: 400;
    color: var(--ink-soft);
  }
  .actions {
    position: absolute;
    left: 42px;
    top: 289px;
    display: flex;
    gap: 16px;
  }
  .button {
    display: flex;
    align-items: center;
    justify-content: center;
    width: 110px;
    height: 32px;
    border-radius: 12px;
    font-size: 13px;
    font-weight: 500;
  }
  .button-primary {
    background: linear-gradient(90deg, var(--green), var(--teal) 60%, var(--blue));
    color: #fff;
  }
  .button-outline {
    background: var(--paper);
    color: var(--ink);
    border: 1.5px solid var(--teal);
  }
  .site-url {
    position: absolute;
    left: 42px;
    top: 348px;
    font-size: 17px;
    font-weight: 600;
    font-style: italic;
    letter-spacing: 5.6px;
    color: var(--green);
  }
</style>
</head>
<body>
  <section class="banner">
    <svg class="banner-shapes" viewBox="0 0 1140 407" xmlns="http://www.w3.org/2000/svg">
      <defs>
        <linearGradient id="photoTone" x1="0" y1="0" x2="1" y2="0">
          <stop offset="0" stop-color="var(--photo-mid)"/>
          <stop offset="0.35" stop-color="var(--photo-dark)"/>
          <stop offset="0.7" stop-color="var(--photo-light)"/>
          <stop offset="1" stop-color="var(--photo-light)"/>
        </linearGradient>
        <linearGradient id="stripeTone" x1="0" y1="0" x2="0.3" y2="1">
          <stop offset="0" stop-color="var(--green)"/>
          <stop offset="0.5" stop-color="var(--teal)"/>
          <stop offset="1" stop-color="var(--blue)"/>
        </linearGradient>
        <linearGradient id="bandTone" x1="0" y1="0" x2="1" y2="0">
          <stop offset="0" stop-color="var(--green)"/>
          <stop offset="0.45" stop-color="var(--teal)"/>
          <stop offset="1" stop-color="var(--blue)"/>
        </linearGradient>
        <linearGradient id="baseTone" x1="0" y1="0" x2="1" y2="0">
          <stop offset="0" stop-color="var(--teal)"/>
          <stop offset="1" stop-color="var(--blue)"/>
        </linearGradient>
      </defs>
      <polygon class="hero-photo" role="img" aria-label="Photo of a businessman in a suit working on a laptop at a white desk beside a bright office window" points="436,0 1140,0 1140,407 656,407" fill="url(#photoTone)"/>
      <polygon class="accent-stripe" points="383,0 436,0 656,407 605,407" fill="url(#stripeTone)" opacity="0.92"/>
      <polygon class="social-band" points="824,0 1140,0 1140,43 846,43" fill="url(#bandTone)"/>
      <g class="social-links" fill="#ffffff">
        <circle cx="913" cy="21" r="9"/>
        <circle cx="955" cy="21" r="9"/>
        <circle cx="998" cy="21" r="9"/>
        <circle cx="1040" cy="21" r="9"/>
        <circle cx="1083" cy="21" r="9"/>
      </g>
      <rect class="base-band" x="835" y="359" width="305" height="48" fill="url(#baseTone)" opacity="0.85"/>
    </svg>

    <div class="brand">
      <span class="brand-mark"></span>
      <span class="brand-name">LoomDigest.io</span>
    </div>

    <h1 class="headline"><strong>Our</strong> Business</h1>

    <p class="intro">Lorem ipsum dolor sit amet, copiosae vitu-perata vix an. Postea bonorum placerat cu his, nam quas recteque in, ea sea iuvaret mandamus.</p>

    <div class="actions">
      <span class="button button-primary">SKIP</span>
      <span class="button button-outline">MORE</span>
    </div>

    <p class="site-url">www.loomdigest.io</p>
  </section>
</body>
</html>
```